Design the 21st Harborlight Open Cinema Showcase Poster. Think modern, chic, cool, film, movies - driving people to the film festival - the film festivla is in San Francisco and the SF East Bay. Our logo is attached. Dates will be determined soon . please use - November 2 - 11, 2018 (for placement) Keep in mind abstract, chic, modern - eye catching. website is www.hlocs-fest.org

Target Market(s)

25 - 45 year old - upper middle class

Industry/Entity Type

Film Production

Colors

Designer to choose colors to be used in the design.

Requirements
Must have
• logo (attached) www.hlocs-fest.org - chic modern design
Nice to have
• best coolest poster ever!
Should not have
• CLIP ART!!!

```html
<!DOCTYPE html>
<html lang="en">
<head>
<meta charset="utf-8">
<title>21st Harborlight Open Cinema Showcase</title>
<link rel="stylesheet" href="https://fonts.googleapis.com/css2?family=Teko:wght@300;400;500;600&display=swap">
<style>
  :root {
    --bg-center: #ececec;
    --bg-edge: #cdcdcd;
    --ink: #3b3b3b;
    --red: #d10a0a;
    --reel-dark: #111111;
    --reel-light: #8a8a8a;
    --shadow: rgba(0, 0, 0, 0.45);
  }
  html, body {
    margin: 0;
    padding: 0;
    overflow: hidden;
  }
  .poster {
    position: relative;
    width: 807px;
    height: 1200px;
    overflow: hidden;
    background: radial-gradient(ellipse at 45% 40%, var(--bg-center) 0%, var(--bg-edge) 100%);
    font-family: "Teko", "Arial Narrow", sans-serif;
    color: var(--ink);
  }
  .poster > * { position: absolute; margin: 0; white-space: nowrap; }
  .film-sphere {
    left: 227px;
    top: 94px;
    width: 355px;
    height: 458px;
    border-radius: 46% 46% 48% 48%;
    background: linear-gradient(160deg, var(--reel-light) 0%, var(--reel-dark) 45%, var(--reel-light) 70%, var(--reel-dark) 100%);
  }
  .sphere-shadow {
    left: 316px;
    top: 588px;
    width: 174px;
    height: 24px;
    border-radius: 50%;
    background: radial-gradient(ellipse at center, var(--shadow) 0%, rgba(0,0,0,0) 72%);
  }
  .tagline {
    display: flex;
    align-items: baseline;
    justify-content: flex-end;
    gap: 6px;
    line-height: 1;
    text-transform: uppercase;
  }
  .tagline .plain { font-size: 24px; font-weight: 500; }
  .tagline .accent { font-size: 34px; font-weight: 500; color: var(--red); }
  .tagline-first { right: 304px; top: 636px; }
  .tagline-second { right: 236px; top: 660px; }
  .edition {
    left: 124px;
    top: 686px;
    font-size: 190px;
    font-weight: 500;
    line-height: 1;
    letter-spacing: -6px;
    color: var(--red);
  }
  .name-line {
    line-height: 1;
    font-weight: 400;
    text-transform: uppercase;
  }
  .name-top { left: 283px; top: 793px; font-size: 62px; letter-spacing: 1px; }
  .name-middle { left: 127px; top: 855px; font-size: 52px; letter-spacing: 0.5px; }
  .name-bottom { left: 322px; top: 893px; font-size: 80px; letter-spacing: 1px; }
  .dates {
    left: 322px;
    top: 970px;
    font-size: 46px;
    font-weight: 400;
    line-height: 1;
    letter-spacing: 0.22em;
    color: var(--red);
  }
  .year {
    left: 322px;
    top: 1030px;
    font-size: 50px;
    font-weight: 300;
    line-height: 1;
    letter-spacing: 0.3em;
  }
  .website {
    left: 322px;
    top: 1100px;
    font-size: 26px;
    font-weight: 400;
    line-height: 1;
    letter-spacing: 0.08em;
  }
</style>
</head>
<body>
  <main class="poster">
    <div class="film-sphere" role="img" aria-label="Abstract sphere formed by a spiralling strip of black film"></div>
    <div class="sphere-shadow"></div>

    <p class="tagline tagline-first"><span class="plain">Something for</span><span class="accent">Everyone</span></p>
    <p class="tagline tagline-second"><span class="plain">From around</span><span class="accent">The World</span></p>

    <h1 class="edition">21ST</h1>
    <p class="name-line name-top">Harborlight</p>
    <p class="name-line name-middle">Open Cinema</p>
    <p class="name-line name-bottom">Showcase</p>

    <p class="dates">NOVEMBER 2-11,</p>
    <p class="year">2018</p>
    <p class="website">www.hlocs-fest.org</p>
  </main>
</body>
</html>
```